Business card for my new company (Accounting firm)

I need a business card for my new business Brightwell Advisory and Ledger SA. Our services are accounting, tax, audit and financial management. Our customers are small companies, start-ups and new companies. The final design has to show financial security, trust and growth. Please find our logo attached to the business card. Text for the business card: Brightwell Advisory and Ledger SA Tomas Varenholt Director and Founder Certified Accountant Tel. 022 418 57 34 tv@clairevalconseil.ch www.clairevalconseil.ch Rue des Vergières 27 1201 Geneva
Target Market(s)
Our customers are small companies, start-ups and new companies.
Industry/Entity Type
Finance And Accounting
Contact Information for Business Card
Claireval Conseil et Comptes SA
Tomas Varenholt
Directeur et Fondateur
Expert-comptable diplômé
Tél. 022 418 57 34
tv@clairevalconseil.ch
www.clairevalconseil.ch
Rue des Vergières 27
1201 Genève

```html
<!DOCTYPE html>
<html lang="en">
<head>
<meta charset="utf-8">
<title>Claireval Conseil et Comptes – Business Card</title>
<link href="https://fonts.googleapis.com/css2?family=Lato:wght@400;700&display=swap" rel="stylesheet">
<style>
  :root {
    --stage: #262626;
    --card-white: #ffffff;
    --brand-blue: #1d6aa8;
    --ink: #2e2e2e;
    --logo-ink: #3b3b3b;
    --rule: #b9b9b9;
    --icon-blue: #1f5f93;
    --back-top: #2aa9e0;
    --back-bottom: #1a6fb0;
    --pattern-light: rgba(255, 255, 255, 0.07);
    --pattern-dark: rgba(10, 60, 110, 0.10);
  }
  * { margin: 0; padding: 0; box-sizing: border-box; }
  html, body { width: 1200px; height: 1108px; overflow: hidden; }
  body {
    background: var(--stage);
    display: flex;
    align-items: center;
    justify-content: center;
    gap: 80px;
    font-family: "Lato", sans-serif;
  }
  .card {
    width: 400px;
    height: 680px;
    border-radius: 28px;
    position: relative;
    overflow: hidden;
  }
  .card-front {
    background: var(--card-white);
    display: flex;
    flex-direction: column;
    align-items: center;
    padding-top: 88px;
    text-align: center;
    color: var(--ink);
  }
  .brand-mark {
    width: 84px;
    height: 84px;
    border-radius: 50%;
    background: var(--brand-blue);
  }
  .brand-name {
    margin-top: 16px;
    width: 260px;
    font-size: 28px;
    font-weight: 700;
    line-height: 1.15;
    color: var(--logo-ink);
  }
  .holder-name {
    margin-top: 26px;
    font-size: 25px;
    font-weight: 700;
    color: var(--brand-blue);
  }
  .holder-role { font-size: 19px; line-height: 1.2; margin-top: 4px; }
  .contact-icons {
    display: flex;
    align-items: center;
    gap: 8px;
    margin-top: 14px;
    width: 190px;
  }
  .contact-icons::before, .contact-icons::after {
    content: ""; flex: 1; height: 1px; background: var(--rule);
  }
  .contact-icons svg { width: 26px; height: 26px; }
  .contact-lines { font-size: 19px; line-height: 1.25; margin-top: 12px; }
  .rule { width: 190px; height: 1px; background: var(--rule); margin: 12px 0; }
  .address { font-size: 19px; line-height: 1.25; }
  .card-back {
    background: linear-gradient(180deg, var(--back-top) 0%, var(--back-bottom) 100%);
  }
  .back-pattern {
    position: absolute;
    inset: 0;
    background:
      linear-gradient(180deg, var(--pattern-light) 0%, transparent 45%, var(--pattern-dark) 100%);
  }
  .back-name {
    position: absolute;
    left: 0;
    right: 0;
    bottom: 80px;
    margin: 0 auto;
    width: 300px;
    text-align: center;
    font-size: 34px;
    font-weight: 700;
    line-height: 1.15;
    color: #ffffff;
  }
</style>
</head>
<body>
  <section class="card card-front">
    <div class="brand-mark" aria-hidden="true"></div>
    <p class="brand-name">Claireval Conseil et Comptes</p>
    <h1 class="holder-name">SA TOMAS VARENHOLT</h1>
    <p class="holder-role">Director and Founder<br>Certified Accountant</p>
    <div class="contact-icons">
      <svg viewBox="0 0 26 26" aria-label="Phone"><circle cx="13" cy="13" r="13" fill="var(--icon-blue)"/><path d="M8 9c1-2 2-2 3 0l-1 2c1 2 2 3 4 4l2-1c2 1 2 2 0 3-4 1-9-4-8-8z" fill="#fff"/></svg>
      <svg viewBox="0 0 26 26" aria-label="Email"><circle cx="13" cy="13" r="13" fill="var(--icon-blue)"/><rect x="7" y="9" width="12" height="8" fill="#fff"/><path d="M7 9l6 5 6-5" fill="none" stroke="var(--icon-blue)" stroke-width="1.2"/></svg>
      <svg viewBox="0 0 26 26" aria-label="Website"><circle cx="13" cy="13" r="13" fill="var(--icon-blue)"/><circle cx="13" cy="13" r="6" fill="none" stroke="#fff" stroke-width="1.4"/><path d="M7 13h12M13 7c-3 3-3 9 0 12M13 7c3 3 3 9 0 12" fill="none" stroke="#fff" stroke-width="1.2"/></svg>
    </div>
    <p class="contact-lines">022 418 57 34<br>tv@clairevalconseil.ch<br>www.clairevalconseil.ch</p>
    <div class="rule"></div>
    <p class="address">Rue des Vergières 27<br>1201 Geneva</p>
  </section>

  <section class="card card-back">
    <div class="back-pattern" role="img" aria-label="Subtle repeating brand pattern in light and deep blue tones"></div>
    <p class="back-name">Claireval Conseil et Comptes</p>
  </section>
</body>
</html>
```